birchwell hollow cattle company website

we would like a home page, an about us page, a page for sires, a page for dams, A sale page where we can list progreny for sale and a contact us. on the about us page we would like there to be a family picture. on the sires page we would like to have a picture of each sire, a description beside them and a link to their online profile at northern hereford registry. on the dam page we would like to have a picture of each dam, aswell as a description beside them aswell as a link to the northern hereford registry site. would like the website to very mobile phone friendly as expecting most traffic to be on phone. we would like the website to look and feel very mich like a farm, rustic, barbed wire and other farm feels. we would also like a frozen genetics pages where we can include pictures and descriptions of the sires and dams aswell as a price for embryos and semen. we need to website to be easy to maintain so we can update pictures and information as it changes, we would like there to be a feature so that people can sign up to be on our mailing list by giving us their mailing addess and email and full name
aswell as an area where they can send us a message to contact us.

leaving for work for 3 weeks in the canadian arctic will have limited ability to use the internet

Target Market(s)

other ranchers, farmers, cattlemen,

Industry/Entity Type

farming, agriculture, cattle

Coding

Coded - Design and coding required

Requirements
Must have
• about page, contact page, sires page, dams page, SALE page.
Nice to have
• country/farm vibe, barbed wire, wood,

```html
<!DOCTYPE html>
<html lang="en">
<head>
<meta charset="utf-8">
<title>Birchwell Hollow Cattle Company — Website Pages</title>
<link href="https://fonts.googleapis.com/css2?family=Crimson+Pro:wght@400;500&family=Figtree:wght@400;500;600&display=swap" rel="stylesheet">
<style>
:root{
  --stage:#8a8a8a;
  --green:#2f8f1f;
  --green-dark:#1f3a1c;
  --green-soft:#cdeec3;
  --ink:#1c2619;
  --muted:#5d6a58;
  --light:#f3fbef;
  --band:#e6f2e1;
  --white:#ffffff;
  --black:#000000;
  --line:#dfe7da;
}
*{box-sizing:border-box;margin:0;padding:0}
html,body{width:1200px;height:1095px;overflow:hidden;background:var(--stage)}
body{position:relative;font-family:'Figtree',sans-serif;color:var(--ink)}
.page{position:absolute;width:317px;background:var(--light);overflow:hidden}
.page--home{left:83px;top:83px;height:929px}
.page--about{left:441px;top:83px;height:833px}
.page--contact{left:800px;top:83px;height:389px}
.a{position:absolute}
.serif{font-family:'Crimson Pro',serif;font-weight:400}
.photo{position:absolute;border-radius:3px}
/* nav */
.brand{position:absolute;left:32px;top:6px;width:26px;font-family:'Crimson Pro',serif;font-size:3.4px;line-height:1.1;color:var(--white);text-align:center}
.brand i{display:block;width:9px;height:9px;margin:0 auto 1px;border:0.6px solid var(--white);border-radius:50%}
.nav a{position:absolute;top:11px;font-size:3.2px;color:var(--white);text-decoration:none}
.nav .login{top:8px;width:21px;height:8px;background:var(--green);border-radius:1px;text-align:center;line-height:8px;font-family:'Crimson Pro',serif}
.hero-title{color:var(--white);font-size:12px;text-align:center;width:100%}
.crumb{color:#d9d9d9;font-size:3px;text-align:center;width:100%}
.h2{font-family:'Crimson Pro',serif;font-size:12px;line-height:11.5px;color:var(--ink)}
.p{font-size:2.8px;line-height:4.3px;color:var(--muted)}
.btn{position:absolute;background:var(--green);color:var(--white);font-family:'Crimson Pro',serif;font-size:3px;text-align:center;border-radius:1.5px}
.btn-outline{position:absolute;border:0.7px solid var(--green);color:var(--green);font-family:'Crimson Pro',serif;font-size:3px;text-align:center;border-radius:1.5px;background:var(--white)}
.stat-num{font-family:'Crimson Pro',serif;font-size:8px}
.stat-label{font-size:2.9px}
.card{position:absolute;background:var(--white);border-radius:3px;box-shadow:0 0.5px 2px rgba(0,0,0,.06)}
.input{position:absolute;background:#f2f4f1;border:0.4px solid var(--line);border-radius:1.5px;font-size:2.6px;color:#9aa094;padding:1.6px 2.5px}
.label{position:absolute;font-size:2.6px;color:var(--ink)}
.arrow-btn{position:absolute;width:9px;height:7px;border:0.5px solid #9aa39a;border-radius:1px;font-size:3.5px;line-height:6px;text-align:center;color:var(--ink);background:var(--white)}
.icon-dot{position:absolute;width:12px;height:12px;border-radius:50%;background:var(--green-soft)}
/* footer */
.footer{position:absolute;left:0;width:317px;height:86px;background:var(--black);color:var(--white)}
.footer .fname{position:absolute;left:32px;top:24px;width:40px;font-family:'Crimson Pro',serif;font-size:5px;line-height:5.5px}
.footer .social{position:absolute;top:56px;width:8px;height:8px;border-radius:50%;background:var(--green)}
.footer .fh{position:absolute;top:19px;font-family:'Crimson Pro',serif;font-size:3.4px}
.footer .fl{position:absolute;font-size:2.6px;line-height:6.6px;color:#d8d8d8}
.footer .sub-input{position:absolute;left:228px;top:46px;width:57px;height:7px;border:0.4px solid #444;border-radius:1px;font-size:2.2px;color:#aaa;padding:2px}
.footer .sub-btn{position:absolute;left:269px;top:47px;width:15px;height:5px;background:var(--white);color:var(--ink);font-size:2.2px;text-align:center;line-height:5px;border-radius:1px}
.footer .rule{position:absolute;left:32px;right:32px;top:73px;height:0.4px;background:#333}
.footer .copy{position:absolute;top:78px;font-size:2.6px;color:#ccc}
</style>
</head>
<body>

<!-- ================= HOME ================= -->
<section class="page page--home" aria-label="Home page">
  <div class="a" role="img" aria-label="Red bull standing in a hay barn at dusk" style="left:0;top:0;width:317px;height:186px;background:linear-gradient(100deg,#2c2a26 0%,#3d342a 45%,#4a3a2a 70%,#2f2a24 100%)"></div>
  <div class="brand"><i></i>BIRCHWELL HOLLOW<br>CATTLE COMPANY</div>
  <nav class="nav">
    <a style="left:130px">Home</a><a style="left:150px">About Us</a><a style="left:176px">Sires</a><a style="left:195px">Dams</a><a style="left:215px">Sale</a><a style="left:234px">Contact Us</a><a class="login" style="left:264px">Login</a>
  </nav>
  <p class="a" style="left:32px;top:52px;font-family:'Crimson Pro',serif;font-size:3.6px;color:#eee">Established 1978</p>
  <h1 class="a serif" style="left:32px;top:57px;font-size:16.5px;line-height:15.5px;color:var(--white)">Premium Heritage<br>Cattle Genetics</h1>
  <p class="a" style="left:32px;top:97px;width:125px;font-size:2.9px;line-height:4.3px;color:#ddd">Breeding excellence in every head. Experience the rustic tradition and superior quality of our family-owned ranch in the heart of the heartland.</p>
  <div class="a" style="left:32px;top:117px;color:var(--white)"><div class="stat-num">500+</div><div class="stat-label" style="margin-top:1px">Healthy Sires &amp; Dams</div></div>
  <div class="a" style="left:72px;top:117px;color:var(--white)"><div class="stat-num">1,200+</div><div class="stat-label" style="margin-top:1px">Farmers &amp; Ranchers Served</div></div>
  <div class="a" style="left:121px;top:117px;color:var(--white)"><div class="stat-num">3M+</div><div class="stat-label" style="margin-top:1px">Calves Bred Successfully</div></div>
  <div class="btn" style="left:32px;top:142px;width:28px;height:10px;line-height:10px">View Animals</div>
  <div class="btn" style="left:62px;top:142px;width:28px;height:10px;line-height:10px;background:#5a5248">Current Sales</div>
  <div class="a" style="left:207px;top:98px;width:78px;height:54px;border:0.5px solid #8b8378;border-radius:3px;background:rgba(70,62,54,.55)">
    <div class="a" style="left:10px;top:10px;width:10px;height:10px;background:var(--green);border-radius:1.5px"></div>
    <p class="a" style="left:24px;top:11px;font-size:3.6px;line-height:4.8px;color:var(--white)">Quality Cattle Raised<br>with Care</p>
    <p class="a" style="left:10px;top:28px;width:60px;font-size:2.4px;line-height:3.6px;color:#cfc7bb">Our farm is dedicated to raising healthy cattle with strong genetics, trusted by farmers and ranchers for quality breeding and livestock.</p>
  </div>

  <div class="photo" role="img" aria-label="Cattle grazing in a pasture at sunset" style="left:33px;top:205px;width:91px;height:99px;background:linear-gradient(180deg,#e8a562 0%,#c98a56 30%,#6e8a4a 55%,#3f6a2c 100%)"></div>
  <div class="photo" role="img" aria-label="Dairy cattle inside a barn" style="left:79px;top:256px;width:66px;height:77px;background:linear-gradient(180deg,#a9a8a2 0%,#6d6a62 50%,#4f4c46 100%);border:2px solid var(--light)"></div>
  <div class="card" style="left:33px;top:311px;width:85px;height:57px">
    <div class="a" style="left:9px;top:7px;width:10px;height:10px;background:var(--green);border-radius:1.5px"></div>
    <p class="a serif" style="left:9px;top:20px;font-size:4.6px;line-height:5.4px">Trusted Breeding &amp; Livestock<br>Services</p>
    <p class="a p" style="left:9px;top:33px;width:64px;font-size:2.4px;line-height:3.7px">With a deep respect for the land and a commitment to raising healthy, high-quality cattle, we support farmers and ranchers with superior genetics and reliable breeding stock.</p>
  </div>
  <h2 class="a h2" style="left:161px;top:206px">Grown from the Soil,<br>Raised with Integrity</h2>
  <p class="a p" style="left:161px;top:235px;width:124px">Nestled in the heart of the rolling hills, our cattle farm is dedicated to sustainable ranching and superior genetics. We take pride in our rustic heritage and the quality of our Sires and Dams.</p>
  <p class="a p" style="left:161px;top:259px;width:124px">For over four decades, the Hartley family has focused on raising cattle that thrive in diverse environments, prioritizing health, docility, and growth performance.</p>
  <p class="a stat-num" style="left:161px;top:292px;font-size:11px;color:var(--green)">50+</p>
  <p class="a" style="left:161px;top:312px;font-size:3.6px">Healthy Sires &amp; Dams</p>
  <p class="a stat-num" style="left:161px;top:329px;font-size:11px;color:var(--green)">1000+</p>
  <p class="a" style="left:161px;top:349px;font-size:3.6px">Calves Bred Successfully</p>
  <div class="photo" role="img" aria-label="Ranch family standing in front of a wooden barn" style="left:225px;top:290px;width:60px;height:64px;background:linear-gradient(180deg,#7a5a3c 0%,#5b4330 60%,#3e3226 100%)"></div>

  <div class="a" style="left:0;top:389px;width:317px;height:148px;background:var(--band)"></div>
  <h2 class="a h2" style="left:0;top:401px;width:317px;text-align:center">Featured Sires &amp; Dams</h2>
  <p class="a p" style="left:0;top:416px;width:317px;text-align:center">Discover our top-quality bulls, selected for superior genetics and strong growth performance.</p>
  <div class="card" style="left:32px;top:426px;width:81px;height:97px;overflow:hidden">
    <div class="a" role="img" aria-label="Black bull in a green pasture" style="left:0;top:0;width:81px;height:54px;background:linear-gradient(180deg,#b9d3e6 0%,#8aa86a 55%,#2a2a26 100%)"></div>
    <p class="a serif" style="left:5px;top:58px;font-size:5px">Midnight Express 402</p>
    <p class="a p" style="left:5px;top:66px;width:72px;font-size:2.4px;line-height:3.6px">A strong Angus bull with excellent growth and docile temperament.</p>
    <div class="btn-outline" style="left:5px;top:81px;width:71px;height:11px;line-height:10px">View Profile</div>
  </div>
  <div class="card" style="left:118px;top:426px;width:81px;height:97px;overflow:hidden">
    <div class="a" role="img" aria-label="White cow standing in a grassy field" style="left:0;top:0;width:81px;height:54px;background:linear-gradient(180deg,#6ea6d8 0%,#c9d7c4 55%,#5e9a3e 100%)"></div>
    <p class="a serif" style="left:5px;top:58px;font-size:5px">Bella Rose 012</p>
    <p class="a p" style="left:5px;top:66px;width:72px;font-size:2.4px;line-height:3.6px">A strong Angus bull with excellent growth and docile temperament.</p>
    <div class="btn-outline" style="left:5px;top:81px;width:71px;height:11px;line-height:10px">View Profile</div>
  </div>
  <div class="card" style="left:204px;top:426px;width:81px;height:97px;overflow:hidden">
    <div class="a" role="img" aria-label="Red bull standing on grass" style="left:0;top:0;width:81px;height:54px;background:linear-gradient(180deg,#a8c8e2 0%,#a9663a 50%,#5c8a3a 100%)"></div>
    <p class="a serif" style="left:5px;top:58px;font-size:5px">Ironclad 77</p>
    <p class="a p" style="left:5px;top:66px;width:72px;font-size:2.4px;line-height:3.6px">A strong Angus bull with excellent growth and docile temperament.</p>
    <div class="btn-outline" style="left:5px;top:81px;width:71px;height:11px;line-height:10px">View Profile</div>
  </div>

  <div class="a" style="left:32px;top:557px;width:253px;height:123px;border-radius:4px;overflow:hidden;background:var(--green-dark)">
    <div class="a" role="img" aria-label="Hereford cattle in a feeding barn" style="left:126px;top:0;width:127px;height:123px;background:linear-gradient(180deg,#6a6558 0%,#6a3f26 45%,#8f6a3a 80%,#b89a5a 100%)"></div>
    <p class="a" style="left:17px;top:17px;font-size:2.4px;color:#6aa25c">● Animals for Sale</p>
    <h2 class="a serif" style="left:17px;top:23px;font-size:12px;line-height:11.5px;color:var(--white)">Your Next Prize<br>Bull or Cow<br>Awaits!</h2>
    <p class="a" style="left:17px;top:64px;width:95px;font-size:2.6px;line-height:3.7px;color:#e3eadf">Every animal on our farm is raised with care and attention, ensuring strong health, excellent genetics, and a calm temperament. From energetic young bulls ready for breeding to nurturing cows with proven mothering skills, we provide livestock that will thrive on your ranch. Explore our selection today and bring home the best for your farm.</p>
    <div class="btn" style="left:17px;top:96px;width:48px;height:10px;line-height:10px">Explore Animals for Sale</div>
  </div>

  <h2 class="a h2" style="left:0;top:698px;width:317px;text-align:center">Get in Touch</h2>
  <p class="a p" style="left:0;top:713px;width:317px;text-align:center">Have questions or want to inquire about our bulls, cows, or breeding stock? Fill out the form below and we'll get back to you promptly.</p>
  <div class="photo" role="img" aria-label="Map of the ranch location" style="left:32px;top:724px;width:124px;height:98px;background:linear-gradient(135deg,#eceeea,#dfe3dc)"></div>
  <div class="a" style="left:160px;top:724px;width:125px;height:98px;background:#eef3ec;border-radius:3px">
    <span class="label" style="left:5px;top:5px">Full Name</span>
    <div class="input" style="left:5px;top:9px;width:115px;height:8px">Please enter your name</div>
    <span class="label" style="left:5px;top:21px">Phone Number</span>
    <div class="input" style="left:5px;top:25px;width:115px;height:8px">Please enter your phone number</div>
    <span class="label" style="left:5px;top:37px">Email Address</span>
    <div class="input" style="left:5px;top:41px;width:115px;height:8px">Please enter your email ID</div>
    <span class="label" style="left:5px;top:53px">Message</span>
    <div class="input" style="left:5px;top:57px;width:115px;height:22px">Please write your message here</div>
    <div class="btn" style="left:5px;top:84px;width:31px;height:10px;line-height:10px">Submit Now</div>
  </div>

  <footer class="footer" style="top:843px">
    <p class="fname">BIRCHWELL HOLLOW CATTLE COMPANY</p>
    <span class="social" style="left:32px"></span><span class="social" style="left:45px"></span><span class="social" style="left:57px"></span>
    <p class="fh" style="left:99px">Quick Links</p>
    <p class="fl" style="left:99px;top:24px">Home<br>About Us<br>Sires<br>Dams<br>Sale<br>Frozen Genetics<br>Contact</p>
    <p class="fh" style="left:151px">Contact Information</p>
    <p class="fl" style="left:151px;top:24px;line-height:8.5px">Phone: (+00) 123 456 789<br>Email: info@birchwellhollow.com<br>Address: 1234, Ranch Road, City, Country</p>
    <p class="fh" style="left:228px">Subscribe To Newsletter</p>
    <p class="fl" style="left:228px;top:25px;width:57px;line-height:3.6px;font-size:2.2px">Stay informed with the latest ranch news, expert tips.</p>
    <div class="sub-input">Email Address *</div><div class="sub-btn">Subscribe</div>
    <div class="rule"></div>
    <p class="copy" style="left:32px">Copyright © 2026 Birchwell Hollow. All Rights Reserved.</p>
    <p class="copy" style="left:196px">FAQ's &nbsp;&nbsp; / &nbsp;&nbsp; Privacy Policy &nbsp;&nbsp; / &nbsp;&nbsp; Terms And Conditions</p>
  </footer>
</section>

<!-- ================= ABOUT ================= -->
<section class="page page--about" aria-label="About us page">
  <div class="a" role="img" aria-label="Rows of dairy cattle in a long barn" style="left:0;top:0;width:317px;height:107px;background:linear-gradient(180deg,#2b2a27 0%,#4a4640 50%,#3a3631 100%)"></div>
  <div class="brand"><i></i>BIRCHWELL HOLLOW<br>CATTLE COMPANY</div>
  <nav class="nav">
    <a style="left:130px">Home</a><a style="left:150px">About Us</a><a style="left:176px">Sires</a><a style="left:195px">Dams</a><a style="left:215px">Sale</a><a style="left:234px">Contact Us</a><a class="login" style="left:264px">Login</a>
  </nav>
  <h1 class="a serif hero-title" style="top:49px">About Us</h1>
  <p class="a crumb" style="top:68px">Home / About Us</p>

  <h2 class="a h2" style="left:33px;top:128px">Grown from the Soil,<br>Raised with Integrity</h2>
  <p class="a p" style="left:33px;top:157px;width:124px">Nestled in the heart of the rolling hills, our cattle farm is dedicated to sustainable ranching and superior genetics. We take pride in our rustic heritage and the quality of our Sires and Dams.</p>
  <p class="a p" style="left:33px;top:182px;width:124px">For over four decades, the Hartley family has focused on raising cattle that thrive in diverse environments, prioritizing health, docility, and growth performance.</p>
  <div class="a" style="left:33px;top:205px"><div class="stat-num">500+</div><div class="stat-label" style="font-size:2.4px">Healthy Sires &amp; Dams</div></div>
  <div class="a" style="left:75px;top:205px"><div class="stat-num">1,200+</div><div class="stat-label" style="font-size:2.4px">Farmers &amp; Ranchers Served</div></div>
  <div class="a" style="left:121px;top:205px"><div class="stat-num">3M+</div><div class="stat-label" style="font-size:2.4px">Calves Bred Successfully</div></div>
  <div class="photo" role="img" aria-label="Ranch family portrait in front of a wooden barn" style="left:168px;top:128px;width:117px;height:88px;background:linear-gradient(180deg,#7e5e40 0%,#5a4330 55%,#2f3a2a 100%)"></div>
  <div class="a" style="left:162px;top:202px;width:33px;height:20px;background:var(--green);border-radius:1.5px">
    <span class="a" style="left:4px;top:3px;width:4px;height:4px;border:0.5px solid var(--white);border-radius:50%"></span>
    <p class="a" style="left:4px;top:10px;font-size:2px;line-height:2.8px;color:var(--white)">Certified Sustainable<br>Ranching Practices</p>
  </div>

  <div class="a" style="left:0;top:286px;width:317px;height:229px;background:var(--band)"></div>
  <div class="photo" role="img" aria-label="Rancher feeding cattle in a barn" style="left:32px;top:242px;width:253px;height:106px;background:linear-gradient(90deg,#5c4a3a 0%,#8a7a66 40%,#6a6a5e 70%,#8d7a5a 100%)"></div>
  <svg class="a" style="left:150px;top:287px" width="16" height="16" viewBox="0 0 16 16"><circle cx="8" cy="8" r="7.4" fill="rgba(255,255,255,.25)" stroke="#fff" stroke-width=".6"/><path d="M6.5 5.2 L11 8 L6.5 10.8Z" fill="#fff"/></svg>
  <div class="photo" role="img" aria-label="Cattle grazing beside a fence in a green pasture" style="left:33px;top:364px;width:123px;height:81px;background:linear-gradient(180deg,#b9d6ec 0%,#7aa55a 45%,#4c7a30 100%)"></div>
  <h2 class="a h2" style="left:162px;top:368px;font-size:11px">Our Mission &amp; Values</h2>
  <p class="a p" style="left:162px;top:384px;width:124px">Our farm is built on generations of knowledge, dedication, and a love for cattle. We focus on raising healthy, well-bred bulls and cows that thrive in diverse environments. Every animal is nurtured with care to ensure strong genetics, excellent health, and calm temperaments.</p>
  <p class="a p" style="left:162px;top:414px;width:124px">We take pride in sustainable ranching practices, preserving the land, and maintaining the rustic heritage of our farm. Our goal is to provide farmers and ranchers with superior breeding stock that enhances their herd and supports long-term success.</p>
  <span class="icon-dot" style="left:67px;top:464px"></span>
  <span class="icon-dot" style="left:153px;top:464px"></span>
  <span class="icon-dot" style="left:239px;top:464px"></span>
  <p class="a serif" style="left:33px;top:481px;width:80px;text-align:center;font-size:4.4px">100% Grass-Fed</p>
  <p class="a serif" style="left:119px;top:481px;width:80px;text-align:center;font-size:4.4px">No Hormones</p>
  <p class="a serif" style="left:205px;top:481px;width:80px;text-align:center;font-size:4.4px">Sustainable Water</p>
  <p class="a p" style="left:33px;top:490px;width:80px;text-align:center;font-size:2.4px;line-height:3.8px">Our animals roam freely on native grasses, ensuring natural growth and premium quality.</p>
  <p class="a p" style="left:119px;top:490px;width:80px;text-align:center;font-size:2.4px;line-height:3.8px">Pure, honest ranching. We never use growth hormones or unnecessary antibiotics.</p>
  <p class="a p" style="left:205px;top:490px;width:80px;text-align:center;font-size:2.4px;line-height:3.8px">We utilize natural spring water and advanced irrigation to protect our local ecosystem.</p>

  <h2 class="a h2" style="left:33px;top:531px">Life at the Ranch</h2>
  <span class="arrow-btn" style="left:264px;top:534px">‹</span><span class="arrow-btn" style="left:276px;top:534px">›</span>
  <div class="photo" role="img" aria-label="Brown calf standing in tall grass" style="left:33px;top:549px;width:81px;height:82px;background:linear-gradient(180deg,#9fc06e 0%,#9a6238 50%,#6f8a3e 100%)"></div>
  <div class="photo" role="img" aria-label="Rolling prairie hills at sunset" style="left:119px;top:549px;width:81px;height:82px;background:linear-gradient(180deg,#2f4a6e 0%,#d58a4a 35%,#7a6a3a 60%,#a08a4a 100%)"></div>
  <div class="photo" role="img" aria-label="Ranch family sitting on a wooden fence" style="left:205px;top:549px;width:81px;height:82px;background:linear-gradient(180deg,#cfe0e8 0%,#6a8a56 45%,#8a5a3a 100%)"></div>

  <h2 class="a h2" style="left:33px;top:649px">What Our Clients Say</h2>
  <span class="arrow-btn" style="left:264px;top:653px">‹</span><span class="arrow-btn" style="left:276px;top:653px">›</span>
  <div class="card" style="left:33px;top:668px;width:94px;height:59px">
    <p class="a" style="left:9px;top:7px;width:78px;font-size:3.6px;line-height:4.4px">"The bulls we purchased from Hartley Ridge Farm exceeded our expectations. Strong, healthy, and well-bred animals that thrive on our ranch."</p>
    <p class="a" style="left:9px;top:45px;font-size:2.8px">Wade Corliss</p>
    <span class="a" style="left:75px;top:42px;width:11px;height:11px;border-radius:50%;background:#8a8a84"></span>
  </div>
  <div class="card" style="left:137px;top:668px;width:93px;height:59px">
    <p class="a" style="left:9px;top:7px;width:78px;font-size:3.6px;line-height:4.4px">"The bulls we purchased from Hartley Ridge Farm exceeded our expectations. Strong, healthy, and well-bred animals that thrive on our ranch."</p>
    <p class="a" style="left:9px;top:45px;font-size:2.8px">Nora Belvin</p>
    <span class="a" style="left:75px;top:42px;width:11px;height:11px;border-radius:50%;background:#6a6a74"></span>
  </div>
  <div class="card" style="left:240px;top:668px;width:93px;height:59px">
    <p class="a" style="left:9px;top:7px;width:78px;font-size:3.6px;line-height:4.4px;white-space:nowrap">"I've been buying cows from this farm<br>for years. Their dedication to quality<br>and care is unmatched. Highly<br>recommend for any cattle breeder."</p>
    <p class="a" style="left:9px;top:45px;font-size:2.8px">Cal Dunmore</p>
  </div>

  <footer class="footer" style="top:747px">
    <p class="fname">BIRCHWELL HOLLOW CATTLE COMPANY</p>
    <span class="social" style="left:32px"></span><span class="social" style="left:45px"></span><span class="social" style="left:57px"></span>
    <p class="fh" style="left:99px">Quick Links</p>
    <p class="fl" style="left:99px;top:24px">Home<br>About Us<br>Sires<br>Dams<br>Sale<br>Frozen Genetics<br>Contact</p>
    <p class="fh" style="left:151px">Contact Information</p>
    <p class="fl" style="left:151px;top:24px;line-height:8.5px">Phone: (+00) 123 456 789<br>Email: info@birchwellhollow.com<br>Address: 1234, Ranch Road, City, Country</p>
    <p class="fh" style="left:228px">Subscribe To Newsletter</p>
    <p class="fl" style="left:228px;top:25px;width:57px;line-height:3.6px;font-size:2.2px">Stay informed with the latest ranch news, expert tips.</p>
    <div class="sub-input">Email Address *</div><div class="sub-btn">Subscribe</div>
    <div class="rule"></div>
    <p class="copy" style="left:32px">Copyright © 2026 Birchwell Hollow. All Rights Reserved.</p>
    <p class="copy" style="left:196px">FAQ's &nbsp;&nbsp; / &nbsp;&nbsp; Privacy Policy &nbsp;&nbsp; / &nbsp;&nbsp; Terms And Conditions</p>
  </footer>
</section>

<!-- ================= CONTACT ================= -->
<section class="page page--contact" aria-label="Contact us page">
  <div class="a" role="img" aria-label="Long cattle barn with rows of cows" style="left:0;top:0;width:317px;height:107px;background:linear-gradient(180deg,#2a2a28 0%,#4d4a44 50%,#3a3733 100%)"></div>
  <div class="brand"><i></i>BIRCHWELL HOLLOW<br>CATTLE COMPANY</div>
  <nav class="nav">
    <a style="left:130px">Home</a><a style="left:150px">About Us</a><a style="left:176px">Sires</a><a style="left:195px">Dams</a><a style="left:215px">Sale</a><a style="left:234px">Contact Us</a><a class="login" style="left:264px">Login</a>
  </nav>
  <h1 class="a serif hero-title" style="top:49px">Contact Us</h1>
  <p class="a crumb" style="top:68px">Home / Contact Us</p>

  <h2 class="a serif" style="left:32px;top:132px;font-size:8px">Visit Our Farm</h2>
  <p class="a p" style="left:32px;top:144px;width:102px;font-size:3px;line-height:3.8px">We'd love to show you around our heritage cattle operations. Whether you're looking to stock your ranch or just want to see the herd, our gates are open.</p>
  <span class="a" style="left:32px;top:170px;width:9px;height:9px;border-radius:2px;background:var(--green-soft)"></span>
  <p class="a" style="left:48px;top:170px;font-size:3.2px;line-height:4.6px"><b style="font-family:'Crimson Pro',serif">Our Address</b><br><span style="color:var(--muted)">1234, Ranch Road, City, Country</span></p>
  <span class="a" style="left:32px;top:187px;width:9px;height:9px;border-radius:2px;background:var(--green-soft)"></span>
  <p class="a" style="left:48px;top:187px;font-size:3.2px;line-height:4.6px"><b style="font-family:'Crimson Pro',serif">Phone Number</b><br><span style="color:var(--muted)">(+00) 123 456 789</span><br><span style="color:var(--green);font-size:2.3px">Mon-Sat, 7am - 6pm</span></p>
  <span class="a" style="left:32px;top:210px;width:9px;height:9px;border-radius:2px;background:var(--green-soft)"></span>
  <p class="a" style="left:48px;top:210px;font-size:3.2px;line-height:4.6px"><b style="font-family:'Crimson Pro',serif">Email Address</b><br><span style="color:var(--muted)">info@birchwellhollow.com</span></p>
  <div class="photo" role="img" aria-label="Map of the farm location" style="left:32px;top:231px;width:102px;height:44px;background:linear-gradient(135deg,#dfe8dc,#cfdccc)"></div>
  <span class="a" style="left:110px;top:266px;width:20px;height:6px;background:var(--white);font-size:2.3px;text-align:center;line-height:6px;border-radius:1px">View Map</span>

  <div class="card" style="left:143px;top:128px;width:141px;height:154px">
    <h2 class="a serif" style="left:11px;top:9px;font-size:8px">Get in Touch</h2>
    <p class="a p" style="left:11px;top:21px;width:120px;font-size:2.8px;line-height:3.8px">Have questions or want to inquire about our bulls, cows, or breeding stock? Fill out the form below and we'll get back to you promptly.</p>
    <span class="label" style="left:11px;top:42px">Full Name *</span>
    <div class="input" style="left:11px;top:48px;width:57px;height:11px;line-height:7px">John Doe</div>
    <span class="label" style="left:74px;top:42px">Phone Number*</span>
    <div class="input" style="left:74px;top:48px;width:57px;height:11px;line-height:7px">(+00) 123 456 789</div>
    <span class="label" style="left:11px;top:66px">Email Address *</span>
    <div class="input" style="left:11px;top:72px;width:120px;height:11px;line-height:7px;color:var(--ink)">john@example.com</div>
    <span class="label" style="left:11px;top:89px">How can we help? *</span>
    <div class="input" style="left:11px;top:95px;width:120px;height:33px">Tell us about your interest in our herd...</div>
    <div class="btn" style="left:11px;top:138px;width:49px;height:13px;line-height:13px">Send Message ➤</div>
  </div>

  <footer class="footer" style="top:303px">
    <p class="fname">BIRCHWELL HOLLOW CATTLE COMPANY</p>
    <span class="social" style="left:32px"></span><span class="social" style="left:45px"></span><span class="social" style="left:57px"></span>
    <p class="fh" style="left:99px">Quick Links</p>
    <p class="fl" style="left:99px;top:24px">Home<br>About Us<br>Sires<br>Dams<br>Sale<br>Frozen Genetics<br>Contact</p>
    <p class="fh" style="left:151px">Contact Information</p>
    <p class="fl" style="left:151px;top:24px;line-height:8.5px">Phone: (+00) 123 456 789<br>Email: info@birchwellhollow.com<br>Address: 1234, Ranch Road, City, Country</p>
    <p class="fh" style="left:228px">Subscribe To Newsletter</p>
    <p class="fl" style="left:228px;top:25px;width:57px;line-height:3.6px;font-size:2.2px">Stay informed with the latest ranch news, expert tips.</p>
    <div class="sub-input">Email Address *</div><div class="sub-btn">Subscribe</div>
    <div class="rule"></div>
    <p class="copy" style="left:32px">Copyright © 2026 Birchwell Hollow. All Rights Reserved.</p>
    <p class="copy" style="left:196px">FAQ's &nbsp;&nbsp; / &nbsp;&nbsp; Privacy Policy &nbsp;&nbsp; / &nbsp;&nbsp; Terms And Conditions</p>
  </footer>
</section>

</body>
</html>
```